Local Roofing/Construction company business needs new biz card design

We need a new business card design, current cards are from the start of this operation and generic at best. We are a local Construction Company (General Contractor) with a majority of our work originating from insurance claims-exterior finish work is the main focus (Roofs-Siding-Gutters etc). Heavily involved with homeowners and the low ball offers they receive from insurance company's after a insurable event takes place. I have attached some of our original logo file(s) below.

```html
<!DOCTYPE html>
<html lang="en">
<head>
<meta charset="utf-8">
<title>Stonevale Builders – Business Card</title>
<link href="https://fonts.googleapis.com/css2?family=Poppins:wght@400;600;700&display=swap" rel="stylesheet">
<style>
  :root {
    --backdrop: #ababab;
    --card-white: #ffffff;
    --card-dark: #0d1e22;
    --brand-green: #31d87a;
    --ink: #1c1c1c;
    --divider: #d8d8d8;
  }
  * { box-sizing: border-box; margin: 0; padding: 0; }
  html, body {
    width: 1093px; height: 1200px; overflow: hidden;
    background: var(--backdrop);
    font-family: "Poppins", sans-serif;
  }
  .card {
    position: absolute;
    left: 265px;
    width: 578px;
    height: 356px;
    border-radius: 27px;
  }
  .card--front { top: 226px; background: var(--card-white); }
  .card--back { top: 621px; background: var(--card-dark); }

  .brand {
    position: absolute;
    display: flex;
    align-items: center;
    gap: 12px;
  }
  .brand__square {
    width: 34px; height: 34px;
    background: var(--brand-green);
    flex: none;
  }
  .brand__name {
    color: var(--brand-green);
    font-weight: 700;
    font-size: 26px;
    line-height: 1.05;
    letter-spacing: 0.5px;
  }
  .card--front .brand { left: 56px; top: 140px; }
  .card--back .brand { left: 50%; top: 50%; transform: translate(-50%, -50%); }
  .card--back .brand__name { font-size: 30px; }
  .card--back .brand__square { width: 40px; height: 40px; }

  .divider {
    position: absolute;
    left: 288px; top: 74px;
    width: 1px; height: 208px;
    background: var(--divider);
  }
  .contact {
    position: absolute;
    left: 311px; top: 88px;
    color: var(--ink);
  }
  .contact__name {
    color: var(--brand-green);
    font-weight: 600;
    font-size: 22px;
    line-height: 26px;
    letter-spacing: 0.2px;
  }
  .contact__role { font-size: 17px; line-height: 20px; margin-bottom: 12px; }
  .contact__list { list-style: none; }
  .contact__item {
    display: flex; align-items: center; gap: 7px;
    font-size: 17px; line-height: 21px;
  }
  .contact__item svg { width: 15px; height: 15px; flex: none; }
  .contact__highlight { color: var(--brand-green); }
  .contact__address { font-size: 17px; line-height: 21px; margin-top: 13px; padding-left: 1px; }
</style>
</head>
<body>
  <section class="card card--front">
    <div class="brand">
      <span class="brand__square"></span>
      <span class="brand__name">STONEVALE<br>BUILDERS</span>
    </div>
    <span class="divider"></span>
    <div class="contact">
      <p class="contact__name">MARCUS HALE</p>
      <p class="contact__role">Managing Director</p>
      <ul class="contact__list">
        <li class="contact__item">
          <svg viewBox="0 0 16 16" aria-hidden="true"><path d="M4 1.5l2.2 3-1.4 1.6c.8 1.9 2.2 3.3 4.1 4.1l1.6-1.4 3 2.2-1.3 2.4C7 13.5 2.5 9 1.6 2.8z" fill="none" stroke="#31d87a" stroke-width="1.4" stroke-linejoin="round"/></svg>
          044-987 654 321
        </li>
        <li class="contact__item">
          <svg viewBox="0 0 16 16" aria-hidden="true"><rect x="1" y="3.5" width="14" height="9" fill="#31d87a"/><path d="M1 3.5l7 5 7-5" fill="none" stroke="#fff" stroke-width="1.2"/></svg>
          hello@stonevale.com
        </li>
        <li class="contact__item">
          <svg viewBox="0 0 16 16" aria-hidden="true"><g fill="none" stroke="#31d87a" stroke-width="1.2"><circle cx="8" cy="8" r="6.5"/><ellipse cx="8" cy="8" rx="3" ry="6.5"/><path d="M1.5 8h13M2.6 4.5h10.8M2.6 11.5h10.8"/></g></svg>
          <span>www.<span class="contact__highlight">stonevalebuild</span>.com</span>
        </li>
      </ul>
      <p class="contact__address">88, Ridgeway Avenue North<br>45452, Westmoor</p>
    </div>
  </section>

  <section class="card card--back">
    <div class="brand">
      <span class="brand__square"></span>
      <span class="brand__name">STONEVALE<br>BUILDERS</span>
    </div>
  </section>
</body>
</html>
```